Accountant website

Please design a accountant website for www.fenwaybridgeadvisory.com.au. This site is majorly out of date, and is not supported by modern browsers.

The style should use the reds from the design at dev.fenwaybridgeadvisory.com.au, and should be modern and make use of Slides (large content slides that the user scrolls through on the front page).

The content is largely already on the site, however happy to move some around to suit the modern design as required.

The dev.fenwaybridgeadvisory.com.au was a rough mock up that I have completed that the client is "happy" with the direction, however this needs a lot of polish and finishing touches, and I will accept designs that differ from this, but highly recommend that this is used as a guide.

Ready to be sliced PSD Only - HTML no required.

In all honesty, although I can technically do a lot of this, the polished finished I want for this site has eluded me in a few attempts, and therefore I am looking out there at you much more artistic people to finish (or redesign if required) this site.

Target Market(s)

Higher end Small - Medium Business

Industry/Entity Type

Accountant

Requirements
Must have
• Must use the logo from dev.fenwaybridgeadvisory.com.au use exactly the red colours as defined in this layout. A basic layout PSD (to get the colour etc) and the logo in ai format is attached to this project. Please ignore the SSL warning on the development site.

The final product does NOT have to be the same as shown on dev.fenwaybridgeadvisory.com.au however the red colour scheme must be used. The client DOES want the logo on the RIGHT.

Must have a front landing page design, and a page layout that considers the other page content (at least one separate PSD)
Nice to have
• I really am looking at a slide format for the front page simular to:

http://www.quillo.com/au/
http://www.vaultmoor.com/

The attached photos should be used on the site. Was considering a rotating banner with these images are a watermark background on a solid Red header bar, but happy to be shown other options.
Should not have
• Please no "Layout Goblin" submissions.

```html
<!DOCTYPE html>
<html lang="en">
<head>
<meta charset="utf-8">
<title>Fenway Bridge Advisory</title>
<link href="https://fonts.googleapis.com/css2?family=Oswald:wght@300;400;500&family=Ubuntu:ital,wght@0,400;0,500;0,700;1,400;1,500&family=Roboto:ital,wght@0,400;1,400&display=swap" rel="stylesheet">
<style>
:root{
  --red:#b8282c;
  --red-dark:#8e1518;
  --red-bright:#e3161d;
  --ink:#222;
  --grey:#6b6b6b;
  --panel:#eef0f3;
  --footer:#ececec;
  --black:#0d0d0d;
  --white:#fff;
}
*{margin:0;padding:0;box-sizing:border-box}
html,body{width:723px;height:1200px;overflow:hidden;background:var(--white)}
body{position:relative;font-family:"Ubuntu",sans-serif;color:var(--ink)}
.abs{position:absolute}

.site-header{top:0;left:0;width:723px;height:68px;border-bottom:1px solid #333}
.brand{position:absolute;display:flex;align-items:center;gap:7px}
.brand-mark{width:16px;height:16px;background:var(--red)}
.brand-name{font-family:"Ubuntu",sans-serif;font-weight:700;color:var(--ink);line-height:1.05}
.brand-name .big{display:block;font-size:21px;letter-spacing:.5px}
.brand-name .small{display:block;font-size:9px;letter-spacing:.3px}
.site-header .brand{right:48px;top:16px}

.main-nav{top:69px;left:0;width:723px;height:38px;background:var(--red);border-bottom:2px solid #d33;box-shadow:0 1px 0 #7a1114}
.main-nav ul{list-style:none;position:absolute;right:48px;top:0;display:flex;height:38px}
.main-nav li{color:var(--white);font-size:11.6px;line-height:38px;padding:0 7px}
.main-nav li.active{background:var(--red-bright);border-left:1px solid #d55;border-right:1px solid #d55}

.hero{top:110px;left:0;width:723px;height:288px;background:linear-gradient(180deg,#b9c6d1 0%,#8aa2b6 25%,#5d7a93 45%,#49647d 70%,#7d6f60 100%)}
.hero h1{position:absolute;left:55px;top:82px;font-family:"Oswald",sans-serif;font-weight:500;font-size:35px;color:#111;letter-spacing:-.5px}
.hero p{position:absolute;left:55px;top:134px;font-family:"Oswald",sans-serif;font-weight:300;font-size:24px;color:#111;letter-spacing:-.3px}
.slide-dots{position:absolute;left:338px;top:265px;display:flex;gap:5px}
.slide-dots span{width:8px;height:8px;background:#111;border:1px solid #fff}
.slide-dots span.on{background:var(--red-bright)}

.intro{top:398px;left:0;width:723px;height:215px}
.intro-photo{position:absolute;left:0;top:0}
.intro-text{position:absolute;left:333px;width:322px}
.section-title{font-family:"Ubuntu",sans-serif;font-weight:400;color:var(--red);font-size:16.5px;line-height:20px;white-space:nowrap}
.reflect{display:block;transform:scaleY(-1);opacity:.12;height:10px;overflow:hidden;line-height:20px;margin-top:-4px}
.intro-text p{font-size:8.3px;line-height:11.6px;color:var(--grey);margin-top:4px}

.benefits{top:613px;left:0;width:723px;height:225px;background:var(--red)}
.benefit{position:absolute;width:172px}
.benefit-icon{position:absolute;left:-72px;top:-6px;width:63px;height:63px;border-radius:50%;background:radial-gradient(circle at 50% 40%,#a31d21,#5e0b0d);border:2px solid #3c0607;box-shadow:0 2px 3px rgba(0,0,0,.35)}
.benefit-icon svg{position:absolute;left:13px;top:13px}
.benefit h3{font-family:"Oswald",sans-serif;font-weight:500;font-size:14px;line-height:18px;color:var(--white);letter-spacing:-.2px;white-space:nowrap}
.benefit p{font-size:9.2px;line-height:11.3px;color:var(--white);margin-top:2px}
.benefit .more{color:#111;font-size:8.5px;margin-top:2px;display:block}

.lower{top:838px;left:0;width:723px;height:205px;background:var(--panel)}
.testimonial{position:absolute;left:76px;width:280px}
.avatar{position:absolute;left:0;top:0;width:44px;height:44px;border-radius:50%;background:linear-gradient(160deg,#b98a6d,#6f4d3b);border:2px solid #fff}
.quote{position:absolute;left:55px;top:0;width:225px;font-family:"Roboto",sans-serif;font-style:italic;font-size:8.2px;line-height:10.5px;color:#555}
.quote .who{font-style:normal;display:block;margin-top:4px;color:#666}
.quote .who b{color:var(--red);font-weight:400}
.article{position:absolute;left:415px;width:205px;font-family:"Roboto",sans-serif}
.article .meta{display:flex;justify-content:space-between;font-size:8.2px;color:#333}
.article .meta b{color:var(--red);font-family:"Ubuntu",sans-serif;font-style:italic;font-weight:500;font-size:7.8px}
.article p{font-style:italic;font-size:7.9px;line-height:10.4px;color:#555;margin-top:3px}
.article .more{display:block;text-align:right;font-style:italic;color:var(--red);font-size:8px;margin-top:1px}
.archive{position:absolute;left:415px;top:185px;font-family:"Ubuntu",sans-serif;font-style:italic;font-weight:500;font-size:8px;color:#222}

.site-footer{top:1043px;left:0;width:723px;height:127px;background:var(--footer)}
.footer-title{position:absolute;font-size:9.5px;color:var(--red)}
.quick-links{position:absolute;list-style:none;font-size:9.3px;color:#444}
.quick-links li{height:25px}
.quick-links li::before{content:"";display:inline-block;width:3px;height:3px;background:#666;margin-right:6px;vertical-align:middle}
.newsletter p{position:absolute;left:315px;top:34px;width:200px;font-size:8.3px;line-height:11.4px;color:#555}
.email-field{position:absolute;left:315px;top:61px;width:177px;height:24px;background:#f6f6f6;border:1px solid #d6d6d6;font-size:8px;color:#888;padding:6px 8px}
.subscribe{position:absolute;left:315px;top:91px;width:77px;height:23px;background:#6f6f6f;color:#fff;font-size:10.5px;font-weight:500;text-align:center;line-height:23px;letter-spacing:.3px}
.site-footer .brand{left:536px;top:17px}
.badge{position:absolute;left:538px;top:59px;width:42px;height:42px;border-radius:50%;background:var(--red);border:3px solid #7b0f12}
.bottom-bar{top:1170px;left:0;width:723px;height:30px;background:var(--black)}
.bottom-bar p{position:absolute;left:47px;top:9px;font-size:9.5px;color:#ddd}
.social{position:absolute;right:47px;top:7px;display:flex;gap:7px}
.social span{width:16px;height:16px;border-radius:3px;background:#fff}
</style>
</head>
<body>

<header class="site-header abs">
  <div class="brand">
    <span class="brand-mark"></span>
    <span class="brand-name"><span class="big">FENWAY</span><span class="small">BRIDGE ADVISORY</span></span>
  </div>
</header>

<nav class="main-nav abs">
  <ul>
    <li class="active">About Us</li>
    <li>Services</li>
    <li>Working With Us</li>
    <li>Testimonials</li>
    <li>Article Of The Moment</li>
    <li>Client Login</li>
  </ul>
</nav>

<section class="hero abs" role="img" aria-label="Photo of a smiling advisor in a red dress sitting on a harbour jetty with city buildings across the water">
  <h1>BUSINESS CAN BE HARD</h1>
  <p>But we make detailed analysis of your finances easy</p>
  <div class="slide-dots"><span class="on"></span><span></span><span></span><span></span></div>
</section>

<section class="intro abs">
  <svg class="intro-photo" width="330" height="215" viewBox="0 0 330 215">
    <defs>
      <linearGradient id="teamTone" x1="0" y1="0" x2="1" y2="1">
        <stop offset="0" stop-color="#c83b3f"/>
        <stop offset=".55" stop-color="#a5262a"/>
        <stop offset="1" stop-color="#e8e6e4"/>
      </linearGradient>
    </defs>
    <polygon points="0,0 224,0 324,107 228,215 0,215" fill="#d9d9d9"/>
    <polygon points="0,0 220,0 318,107 224,215 0,215" fill="url(#teamTone)" role="img" aria-label="Photo of three team members at the reception desk in front of the company sign"/>
  </svg>
  <div class="intro-text" style="top:10px">
    <h2 class="section-title">Getting to Know Fenway Bridge Advisory</h2>
    <span class="section-title reflect" aria-hidden="true">Getting to Know Fenway Bridge Advisory</span>
    <p>Fenway Bridge Advisory aims to service the needs of its clients by focusing on the present rather than reporting on historical figures. We recognise that business owners benefit from regular contact with their accountant. One who undertakes a hands on approach in working with business owners to improve their business.</p>
  </div>
  <div class="intro-text" style="top:111px">
    <h2 class="section-title">Fenway Bridge Advisory Difference</h2>
    <span class="section-title reflect" aria-hidden="true">Fenway Bridge Advisory Difference</span>
    <p>Not all Accountants are created equally … the Fenway Bridge Advisory difference. Fenway Bridge Advisory takes pride in not following the status quo, the following points are just some of the unique benefits you will experience when working with us.</p>
  </div>
</section>

<section class="benefits abs">
  <div class="benefit" style="left:154px;top:31px">
    <div class="benefit-icon"><svg width="34" height="34" viewBox="0 0 34 34" fill="none" stroke="#fff" stroke-width="3"><rect x="3" y="11" width="16" height="12" rx="6"/><rect x="15" y="11" width="16" height="12" rx="6"/></svg></div>
    <h3>Believing in the here and now</h3>
    <p>A proactive accountant that focuses on providing timely and relevant information.</p>
    <span class="more">more..</span>
  </div>
  <div class="benefit" style="left:459px;top:31px">
    <div class="benefit-icon"><svg width="34" height="34" viewBox="0 0 34 34" fill="none" stroke="#fff" stroke-width="2"><path d="M3 16 L17 4 L31 16"/><path d="M7 13 V30 H27 V13"/><circle cx="17" cy="21" r="5"/><path d="M17 18 V21 H19"/></svg></div>
    <h3>Your Place, In your time</h3>
    <p>There are many variations of passages of lorem Ipsum available, but the majority have alteration in some form.</p>
    <span class="more">more..</span>
  </div>
  <div class="benefit" style="left:154px;top:132px">
    <div class="benefit-icon"><svg width="34" height="34" viewBox="0 0 34 34" fill="none" stroke="#fff" stroke-width="2.4"><rect x="8" y="3" width="18" height="28" rx="2"/><path d="M12 10 H22 M12 15 H22 M12 20 H22 M12 25 H22"/></svg></div>
    <h3>Monthly Billing</h3>
    <p>There are many variations of passages of lorem Ipsum available, but majority have alteration in some.</p>
    <span class="more">more..</span>
  </div>
  <div class="benefit" style="left:459px;top:132px">
    <div class="benefit-icon"><svg width="34" height="34" viewBox="0 0 34 34" fill="none" stroke="#fff" stroke-width="2.6"><path d="M6 12 A12 12 0 1 1 6 22"/><path d="M3 8 L6 13 L11 11"/><path d="M17 10 V18 H23"/></svg></div>
    <h3>We will actually call you back</h3>
    <p>There are many variations of passages of lorem Ipsum available, but majority have alteration</p>
    <span class="more">more..</span>
  </div>
</section>

<section class="lower abs">
  <div class="abs" style="left:76px;top:17px">
    <h2 class="section-title">Client Testimonials
      <svg width="36" height="10" viewBox="0 0 36 10" style="margin-left:8px"><path d="M0 5 L6 0 V3 H13 V7 H6 V10 Z" fill="var(--red-dark)"/><path d="M36 5 L30 0 V3 H23 V7 H30 V10 Z" fill="var(--red-dark)"/></svg>
    </h2>
    <span class="section-title reflect" aria-hidden="true">Client Testimonials</span>
  </div>
  <div class="testimonial" style="top:54px">
    <div class="avatar" role="img" aria-label="Portrait photo of the client"></div>
    <p class="quote">" Lorem Ipsum dolor sit amet, consectetur adipisicing elit,sed do eiusmod tempor incididunt ut labore et dolore magna aliqua."<span class="who"><b>- Miles Hartley</b>, Senior Designer</span></p>
  </div>
  <div class="testimonial" style="top:125px">
    <div class="avatar" role="img" aria-label="Portrait photo of the client"></div>
    <p class="quote">" Lorem Ipsum dolor sit amet, consectetur adipisicing elit,sed do eiusmod tempor incididunt ut labore et dolore magna aliqua."<span class="who"><b>- Miles Hartley</b>, Senior Designer</span></p>
  </div>

  <div class="abs" style="left:415px;top:17px">
    <h2 class="section-title">Articles of the Moment</h2>
    <span class="section-title reflect" aria-hidden="true">Articles of the Moment</span>
  </div>
  <div class="article" style="top:58px">
    <div class="meta"><b>When First Impressions Count...</b><span>March 21, 2013</span></div>
    <p>I attended a local solicitors' office this morning and upon arriving was immediately impressed with the appearance of the reception and waiting area.</p>
    <span class="more">More...</span>
  </div>
  <div class="article" style="top:125px">
    <div class="meta"><b>6 Tips for Naming your Business</b><span>January 18, 2013</span></div>
    <p>I attended a local solicitors' office this morning and upon arriving was immediately impressed with the appearance of the reception and waiting area.</p>
    <span class="more">More...</span>
  </div>
  <span class="archive">View all archived articles</span>
</section>

<footer class="site-footer abs">
  <h4 class="footer-title" style="left:60px;top:14px">Quick Links</h4>
  <ul class="quick-links" style="left:60px;top:30px">
    <li>About Us</li><li>Services</li><li>Working with us</li><li>Contact Us</li>
  </ul>
  <ul class="quick-links" style="left:173px;top:30px">
    <li>Testimonials</li><li>News</li><li>Articles Of the Moment</li><li>Client Login</li>
  </ul>
  <div class="newsletter">
    <h4 class="footer-title" style="left:315px;top:14px">Subscribe for Newsletter</h4>
    <p>Lorem Ipsum dolor sit amet, consectetur do eiusmod tempor incididunt ut labore et dolore</p>
    <div class="email-field">E-mail Address</div>
    <div class="subscribe">SUBSCRIBE</div>
  </div>
  <div class="brand">
    <span class="brand-mark"></span>
    <span class="brand-name"><span class="big">FENWAY</span><span class="small">BRIDGE ADVISORY</span></span>
  </div>
  <div class="badge" role="img" aria-label="Professional accreditation badge"></div>
</footer>

<div class="bottom-bar abs">
  <p>© 2013 fenwaybridgeadvisory &nbsp;|&nbsp; All rights reserved.</p>
  <div class="social"><span></span><span></span><span></span></div>
</div>

</body>
</html>
```